Consulting company business cards

We have a base design, but would be willing to update. We have a new logo/"tag" that needs to be added. Current business card design is attached for reference into our "style."

Industry/Entity Type

Business

Contact Information for Business Card

Should contain name and title, office number, mobile number if appropriate, e-mail, website, physical address, and company logo.

Font styles to use
Other font styles liked:
• See current card design on KorvandBCard

Colors
0455a3
85acd3
aaaaaa

Requirements
Must have
• Our colors are navy blue, gray, and a lighter blue
Nice to have
• Design that I can easily drop in new names/titles as we hire employees.

```html
<!DOCTYPE html>
<html lang="en">
<head>
<meta charset="utf-8">
<title>Torvane Business Card</title>
<link href="https://fonts.googleapis.com/css2?family=Open+Sans:wght@400;600;700;800&display=swap" rel="stylesheet">
<style>
  :root {
    --navy: #04304f;
    --navy-text: #0b3352;
    --light-blue: #85acd3;
    --gray: #aaaaaa;
    --paper: #ffffff;
    --ink: #1c1c1c;
    --backdrop: #e9ebee;
  }
  * { box-sizing: border-box; margin: 0; padding: 0; }
  html, body {
    width: 1200px; height: 864px; overflow: hidden;
    background: var(--backdrop);
    font-family: "Open Sans", Arial, sans-serif;
  }
  .sheet {
    width: 1200px; height: 864px;
    display: flex; flex-direction: column; align-items: center; justify-content: center;
    gap: 40px;
  }
  .card {
    position: relative;
    width: 640px; height: 366px;
    box-shadow: 0 6px 18px rgba(0,0,0,0.18);
    overflow: hidden;
  }
  /* Back side */
  .card-back { background: var(--navy); }
  .card-back .wordmark {
    position: absolute; left: 52px; top: 180px;
    font-weight: 800; font-size: 78px; letter-spacing: 4px;
    color: var(--paper); line-height: 1;
  }
  /* Front side */
  .card-front { background: var(--paper); }
  .brand {
    position: absolute; right: 40px; top: 54px;
    display: flex; flex-direction: column; align-items: flex-end;
  }
  .brand-row { display: flex; align-items: center; gap: 14px; }
  .brand-name {
    font-weight: 800; font-size: 58px; letter-spacing: 3px;
    color: var(--navy-text); line-height: 1;
  }
  .brand-dot {
    width: 44px; height: 44px; border-radius: 50%;
    background: var(--light-blue);
  }
  .tagline {
    margin-top: 6px; margin-right: 58px;
    font-size: 13px; letter-spacing: 3.2px; text-transform: uppercase;
    color: var(--gray);
  }
  .divider {
    position: absolute; left: 0; right: 0; top: 156px;
    height: 2px; background: var(--navy-text);
  }
  .person-name {
    position: absolute; left: 48px; top: 128px;
    font-weight: 700; font-size: 19px; color: var(--navy-text);
  }
  .person-title {
    position: absolute; left: 40px; top: 164px;
    font-size: 13px; color: var(--ink);
  }
  .contact {
    position: absolute; right: 40px; top: 212px;
    list-style: none; text-align: right;
    font-size: 15px; color: var(--ink); line-height: 24px;
  }
  .contact li { display: flex; justify-content: flex-end; align-items: center; gap: 10px; }
  .contact svg { width: 12px; height: 12px; fill: var(--navy-text); }
  .contact .address { margin-right: 22px; }
</style>
</head>
<body>
<main class="sheet">
  <section class="card card-back" aria-label="Card back">
    <div class="wordmark">TORVANE</div>
  </section>

  <section class="card card-front" aria-label="Card front">
    <div class="brand">
      <div class="brand-row">
        <span class="brand-name">TORVANE</span>
        <span class="brand-dot"></span>
      </div>
      <span class="tagline">A Cloud Consulting Company</span>
    </div>

    <div class="person-name">Dana Korvand</div>
    <div class="divider"></div>
    <div class="person-title">Office Manager</div>

    <ul class="contact">
      <li>555.014.2910
        <svg viewBox="0 0 12 12" aria-hidden="true"><path d="M2.5 0.5l2 2.3-1.1 1.3c.7 1.6 2 2.9 3.5 3.6l1.3-1.1 2.3 2-1.3 2.4C4.6 10.6 1.4 7.4 0.4 1.9z"/></svg>
      </li>
      <li>555.014.2971
        <svg viewBox="0 0 12 12" aria-hidden="true"><rect x="3" y="0.5" width="6" height="3.5"/><rect x="0.5" y="4.5" width="11" height="6" rx="1"/><rect x="3" y="8" width="6" height="3.5" fill="#fff"/></svg>
      </li>
      <li>dkorvand@torvanetech.com
        <svg viewBox="0 0 12 12" aria-hidden="true"><path d="M0.5 2.5h11v7h-11z M0.5 2.5l5.5 4 5.5-4" stroke="#fff" stroke-width="0.8"/></svg>
      </li>
      <li>torvanetech.com
        <svg viewBox="0 0 12 12" aria-hidden="true"><circle cx="6" cy="6" r="5.5"/><path d="M1 6h10M6 0.5c-2.5 3-2.5 8 0 11M6 0.5c2.5 3 2.5 8 0 11" stroke="#fff" stroke-width="0.7" fill="none"/></svg>
      </li>
      <li class="address">3150 W 48TH St Brookhaven Indiana 46099</li>
    </ul>
  </section>
</main>
</body>
</html>
```